Business Card for Coastal Tundrabridge Advisory

We need a business card for Coastal Tundrabridge Advisory. The company website address is provided below. The company logo is attached. We provide specialized permafrost services to the mining, transportation, and oil & gas industries. The card should be prepared for:
Matthias Korhonen, PhD.
Coastal Tundrabridge Advisory
PO Box 418259
Quillwater, Alaska 99642
Direct: +1-907-555-0143
Email: mkorhonen@tundrabridgeadvisory.example
Website: www.coastaltundrabridgeadvisory.example

```html
<!DOCTYPE html>
<html lang="en">
<head>
<meta charset="utf-8">
<title>Coastal Tundrabridge Advisory – Business Card</title>
<link rel="stylesheet" href="https://fonts.googleapis.com/css2?family=Montserrat:wght@400;500;600;700&display=swap">
<style>
  :root {
    --backdrop: #e9e7e3;
    --card-dark: #0e1822;
    --card-light: #ffffff;
    --ink: #141414;
    --ink-soft: #3a3a3a;
    --paper-text: #ffffff;
    --shadow: rgba(0, 0, 0, 0.22);
  }
  * { box-sizing: border-box; margin: 0; padding: 0; }
  html, body {
    width: 1200px; height: 676px; overflow: hidden;
    background: var(--backdrop);
    font-family: "Montserrat", sans-serif;
  }
  .canvas {
    width: 1200px; height: 676px;
    display: flex; align-items: center; justify-content: center; gap: 50px;
  }
  .card {
    width: 525px; height: 300px; position: relative;
    box-shadow: 0 10px 28px var(--shadow);
  }
  .card--front {
    background: var(--card-dark);
    display: flex; align-items: center; justify-content: center;
  }
  .brand {
    text-transform: uppercase; font-weight: 700; line-height: 1.15;
    letter-spacing: 0.06em;
  }
  .card--front .brand {
    color: var(--paper-text); font-size: 30px; text-align: left;
  }
  .card--back { background: var(--card-light); color: var(--ink); }
  .holder {
    position: absolute; top: 30px; right: 46px; text-align: right;
  }
  .holder__name { font-weight: 700; font-size: 15px; }
  .holder__role { font-weight: 400; font-size: 11px; color: var(--ink-soft); margin-top: 3px; }
  .edge-tab {
    position: absolute; right: 0; top: 96px; width: 18px; height: 34px; background: var(--ink);
  }
  .card--back .brand {
    position: absolute; left: 34px; top: 92px; color: var(--ink); font-size: 19px;
  }
  .contact {
    position: absolute; left: 34px; top: 172px; list-style: none;
    font-size: 10.5px; color: var(--ink-soft);
  }
  .contact li { display: flex; align-items: center; gap: 8px; margin-bottom: 9px; }
  .contact svg { width: 11px; height: 11px; fill: var(--ink); flex: none; }
  .address {
    position: absolute; right: 46px; bottom: 30px; font-size: 11px; line-height: 1.5;
    color: var(--ink-soft); font-style: normal;
  }
</style>
</head>
<body>
<main class="canvas">
  <section class="card card--front" aria-label="Card front">
    <div class="brand">Coastal Tundrabridge<br>Advisory</div>
  </section>

  <section class="card card--back" aria-label="Card back">
    <div class="holder">
      <div class="holder__name">Matthias Korhonen, PhD.</div>
      <div class="holder__role">Managing Director</div>
    </div>
    <span class="edge-tab"></span>

    <div class="brand">Coastal Tundrabridge<br>Advisory</div>

    <ul class="contact">
      <li>
        <svg viewBox="0 0 24 24" aria-hidden="true"><path d="M6.6 10.8a15.1 15.1 0 0 0 6.6 6.6l2.2-2.2c.3-.3.7-.4 1-.2 1.1.4 2.3.6 3.6.6.6 0 1 .4 1 1V20c0 .6-.4 1-1 1A17 17 0 0 1 3 4c0-.6.4-1 1-1h3.5c.6 0 1 .4 1 1 0 1.3.2 2.5.6 3.6.1.3 0 .7-.2 1z"/></svg>
        +1-907-555-0143
      </li>
      <li>
        <svg viewBox="0 0 24 24" aria-hidden="true"><path d="M2 5h20v14H2zm2 2v.5l8 5 8-5V7zm0 2.8V17h16V9.8l-8 5z"/></svg>
        mkorhonen@tundrabridgeadvisory.example
      </li>
      <li>
        <svg viewBox="0 0 24 24" aria-hidden="true"><path d="M12 2a10 10 0 1 0 0 20 10 10 0 0 0 0-20zm6.9 6h-2.9a15.6 15.6 0 0 0-1.4-3.6A8 8 0 0 1 18.9 8zM12 4c.8 1.2 1.5 2.5 1.9 4h-3.8c.4-1.5 1.1-2.8 1.9-4zM4.3 14a8 8 0 0 1 0-4h3.4a16 16 0 0 0 0 4zm.8 2h2.9c.3 1.3.8 2.5 1.4 3.6A8 8 0 0 1 5.1 16zM8 8H5.1a8 8 0 0 1 4.3-3.6C8.8 5.5 8.3 6.7 8 8zm4 12c-.8-1.2-1.5-2.5-1.9-4h3.8c-.4 1.5-1.1 2.8-1.9 4zm2.3-6H9.7a14.7 14.7 0 0 1 0-4h4.6a14.7 14.7 0 0 1 0 4zm.3 5.6c.6-1.1 1.1-2.3 1.4-3.6h2.9a8 8 0 0 1-4.3 3.6zm1.7-5.6a16 16 0 0 0 0-4h3.4a8 8 0 0 1 0 4z"/></svg>
        www.coastaltundrabridgeadvisory.example
      </li>
    </ul>

    <address class="address">
      PO Box 418259<br>
      Quillwater, Alaska 99642
    </address>
  </section>
</main>
</body>
</html>
```